LEARN Business Skills so you can Earn a good living

size of the poster is 8”x 10.75" plus 0.25" bleed.
Please leave 1 inch on the bottoum for footer
I want a design a poster that will attract people's attention.
I appreciate a creative ad however the ad should not take away from being able to clearly read the text.
-I also appreciate a simple creative ad that is not too busy.
-you can use graphics, vectors, or pictures of real people.
-however, if you use real people it should be a white male that is wearing a white shirt and look like a professional person.

Target Market(s)

Potential young business people

Industry/Entity Type

education

Requirements
Must have
• easy to read the text
Nice to have
• I would like a "creative" simple ad that is easy to be read
Should not have
• pictures of women

```html
<!DOCTYPE html>
<html lang="en">
<head>
<meta charset="utf-8">
<title>Learn It to Earn It – Business Enrichment Course</title>
<link href="https://fonts.googleapis.com/css2?family=Montserrat:wght@400;700;800&family=Satisfy&display=swap" rel="stylesheet">
<style>
  :root {
    --stage: #8f8f8f;
    --wall: #d4d4d4;
    --wall-letter: rgba(255,255,255,0.38);
    --band-top: #3d3d3d;
    --band-bottom: #121212;
    --ink-light: #ffffff;
    --footer: #ffffff;
    --photo-a: #e6e6e6;
    --photo-b: #bdbdbd;
  }
  * { margin: 0; padding: 0; box-sizing: border-box; }
  html, body { width: 1200px; height: 1200px; overflow: hidden; }
  body { background: var(--stage); position: relative; font-family: "Montserrat", sans-serif; }

  .poster {
    position: absolute; left: 176px; top: 40px;
    width: 1267px; height: 1675px;
    transform: scale(0.6687); transform-origin: top left;
    overflow: hidden; background: var(--footer);
  }
  .wall { position: absolute; left: 0; top: 0; width: 1267px; height: 760px; background: var(--wall); overflow: hidden; }
  .wall-word {
    position: absolute; left: 18px; font-weight: 800; font-size: 560px; line-height: 1;
    color: var(--wall-letter); letter-spacing: 10px; white-space: nowrap;
  }
  .wall-word.row-1 { top: -289px; }
  .wall-word.row-2 { top: 200px; }
  .hero-photo { position: absolute; left: 160px; top: 62px; width: 790px; height: 698px; }

  .band {
    position: absolute; left: 0; top: 760px; width: 1267px; height: 765px;
    background: linear-gradient(180deg, var(--band-top) 0%, #2b2b2b 55%, var(--band-bottom) 100%);
  }
  .footer { position: absolute; left: 0; top: 1525px; width: 1267px; height: 150px; background: var(--footer); }

  .headline {
    position: absolute; font-weight: 800; font-size: 218px; line-height: 1; color: var(--ink-light);
    white-space: nowrap; letter-spacing: -2px;
    text-shadow: 8px 14px 18px rgba(0,0,0,0.45);
  }
  .headline.learn { left: 130px; top: 573px; }
  .headline.earn { left: 258px; top: 763px; }
  .connector {
    position: absolute; left: 120px; top: 812px; font-family: "Satisfy", cursive;
    font-size: 150px; line-height: 1; color: var(--ink-light);
    text-shadow: 4px 8px 12px rgba(0,0,0,0.4);
  }

  .course { position: absolute; right: 695px; top: 1019px; text-align: right; color: var(--ink-light); }
  .course-title { font-weight: 700; font-size: 62px; line-height: 68px; }
  .course-tagline { margin-top: 14px; font-weight: 400; font-size: 22px; line-height: 29px; }

  .benefits { position: absolute; left: 687px; top: 1026px; width: 470px; color: var(--ink-light); }
  .benefits-intro { font-weight: 400; font-size: 20px; line-height: 26px; }
  .benefits-list { margin-top: 8px; font-weight: 700; font-size: 42px; line-height: 58px; }

  .topics {
    position: absolute; left: 120px; top: 1358px; width: 1020px; color: var(--ink-light);
    font-weight: 700; font-size: 15px; line-height: 28px; text-transform: uppercase;
  }
</style>
</head>
<body>
  <div class="poster">
    <div class="wall">
      <div class="wall-word row-1">ARN</div>
      <div class="wall-word row-2">ARN</div>
      <svg class="hero-photo" role="img" aria-label="Smiling bearded man in a white polo shirt pointing at himself while holding a laptop" viewBox="0 0 790 698" preserveAspectRatio="none">
        <defs>
          <linearGradient id="heroTone" x1="0" y1="0" x2="0" y2="1">
            <stop offset="0" stop-color="#d9d9d9" stop-opacity="0"/>
            <stop offset="0.25" stop-color="#e8e8e8"/>
            <stop offset="1" stop-color="#c4c4c4"/>
          </linearGradient>
        </defs>
        <rect x="0" y="0" width="790" height="698" fill="url(#heroTone)"/>
      </svg>
    </div>

    <div class="band"></div>
    <div class="footer"></div>

    <div class="headline learn">LEARN IT</div>
    <div class="connector">to</div>
    <div class="headline earn">EARN IT</div>

    <div class="course">
      <div class="course-title">Business<br>Enrichment<br>Course</div>
      <div class="course-tagline">A proven success of helping<br>people in their livelihoods</div>
    </div>

    <div class="benefits">
      <div class="benefits-intro">Business skills that will help you:</div>
      <div class="benefits-list">Get a quality job -<br>start / grow your<br>business-Increase<br>your salary</div>
    </div>

    <div class="topics">
      Business Admiistration – Small Business Management -<br>
      Finance - Investments - Computers- Accounting - Sales &nbsp;Marketing - Project Management Interviewing<br>
      Skills - Business Law -Negotiation – Public Speaking - Import/Export - Information Technoloy -<br>
      Distribution - Marketing &nbsp;- &nbsp;&nbsp;LedgerPro - Real Estate - Health Care-Management - Shoplane
    </div>
  </div>
</body>
</html>
```